Coastal Learner Bureau business cards

Australian company about to start offering its services. We recruit international students to come to study English, vocational education and postgraduate courses in Australia. We help them find the institution and select the right city they want to come to Australia. We are a young, online oriented and supportive agency. Our clients are between 18 and 35 years old, mainly University students, young professionals or people with work experience. We provide much more information that any other agency offer. We administrate a Facebook group with more than 11.000 members that daily ask questions about general information when coming to Australia, while they are here and even after they leave the country

Target Market(s)

International students from South America, Central America and Europe

Industry/Entity Type

Student

Contact Information for Business Card

Tomas Bilbrea
Managing Director
tomas@kelvarin.com.au
www.kelvoria.com.au
+61 491058264
Melbourne, Australia

Font styles to use
Serif
Sans Serif

Colors

Designer to choose colors to be used in the design.

Requirements
Must have
• Horizontal design
• Standard business card size and shape. If font uses green or yellow colours, they will have to match the ones from the logo
Nice to have
• UPDATE: Use the contents of the green image to design one of the card sides. Use our logo in the background of that side as watermark.
• Passport image, or immigration stamps. A picture of the Yarra River (from Melbourne) would be cool as well.
Should not have
• Non-standard business card size and shape
• Not black as the background colour of any sides as we are not a VIP agency or a hight class service. We are orientes to young people and they like colours, pictures, something attractive.
• Vertical design
• NO YELLOW or BLACK AS THE BACKGROUND COLOUR OF ANY SIDE OF THE BIZ CARD

```html
<!DOCTYPE html>
<html lang="en">
<head>
<meta charset="utf-8">
<title>Coastal Learner Bureau business cards</title>
<link href="https://fonts.googleapis.com/css2?family=Jost:wght@400;500;700&display=swap" rel="stylesheet">
<style>
  :root {
    --brand-green: #0f6b3f;
    --brand-yellow: #e7b51f;
    --card-white: #ffffff;
    --ink: #3a3a3a;
    --ink-soft: #555555;
    --stage: #e6e8ea;
    --photo-light: #9db1c4;
    --photo-deep: #3f5f80;
  }
  html, body {
    margin: 0;
    padding: 0;
    width: 1200px;
    height: 1000px;
    overflow: hidden;
    background: var(--stage);
    font-family: "Jost", Arial, sans-serif;
  }
  .canvas {
    position: relative;
    width: 1200px;
    height: 1000px;
  }
  .card {
    position: absolute;
    left: 220px;
    width: 760px;
    height: 434px;
    border-radius: 22px;
    overflow: hidden;
    background: var(--card-white);
    box-shadow: 0 8px 24px rgba(0,0,0,0.15);
  }
  .card--front { top: 50px; }
  .card--back { top: 516px; }

  .front-swoosh {
    position: absolute;
    inset: 0;
    width: 760px;
    height: 434px;
  }
  .identity {
    position: absolute;
    left: 50px;
    top: 62px;
  }
  .identity__name {
    margin: 0;
    font-size: 34px;
    font-weight: 700;
    letter-spacing: 1px;
    text-transform: uppercase;
    color: var(--brand-green);
    line-height: 1;
  }
  .identity__role {
    margin: 6px 0 0;
    font-size: 20px;
    font-weight: 400;
    color: var(--ink);
  }
  .divider {
    position: absolute;
    left: 50px;
    top: 150px;
    width: 600px;
    height: 2px;
    background: var(--brand-green);
  }
  .contacts {
    position: absolute;
    left: 50px;
    top: 168px;
    margin: 0;
    padding: 0;
    list-style: none;
  }
  .contacts li {
    display: flex;
    align-items: center;
    gap: 12px;
    height: 28px;
    font-size: 17px;
    color: var(--ink-soft);
    letter-spacing: 0.3px;
  }
  .contacts svg { width: 14px; height: 14px; flex: none; }
  .brand {
    position: absolute;
    right: 70px;
    top: 78px;
    display: flex;
    align-items: center;
    gap: 10px;
  }
  .brand__dot {
    width: 16px;
    height: 16px;
    border-radius: 50%;
    background: var(--brand-yellow);
  }
  .brand__name {
    font-size: 40px;
    font-weight: 500;
    color: var(--brand-green);
    line-height: 1;
  }
  .location {
    position: absolute;
    left: 560px;
    top: 168px;
    display: flex;
    gap: 8px;
    font-size: 18px;
    color: var(--ink);
    line-height: 1.2;
  }
  .location svg { width: 16px; height: 20px; margin-top: 2px; flex: none; }

  .river-photo {
    position: absolute;
    inset: 14px;
    border-radius: 14px;
    background: linear-gradient(180deg, var(--photo-light) 0%, var(--photo-deep) 100%);
  }
</style>
</head>
<body>
<main class="canvas">

  <section class="card card--front" aria-label="Business card front">
    <svg class="front-swoosh" viewBox="0 0 760 434" aria-hidden="true">
      <path d="M0,262 C200,282 470,322 700,434 L0,434 Z" fill="var(--brand-yellow)"/>
      <path d="M0,276 C200,296 460,336 676,434 L0,434 Z" fill="var(--card-white)"/>
      <path d="M0,290 C190,300 450,340 640,434 L0,434 Z" fill="var(--brand-green)"/>
      <path d="M0,300 C120,305 190,318 230,330 C150,322 70,318 0,318 Z" fill="var(--brand-yellow)"/>
    </svg>

    <div class="identity">
      <h1 class="identity__name">Tomas Bilbrea</h1>
      <p class="identity__role">Managing Director</p>
    </div>

    <div class="divider"></div>

    <ul class="contacts">
      <li>
        <svg viewBox="0 0 14 14"><rect x="3" y="1" width="8" height="12" rx="1.5" fill="none" stroke="var(--brand-green)" stroke-width="1.6"/></svg>
        +61 491058264
      </li>
      <li>
        <svg viewBox="0 0 14 14"><rect x="1" y="3" width="12" height="8" rx="1" fill="var(--brand-green)"/><path d="M1,3 L7,8 L13,3" fill="none" stroke="#fff" stroke-width="1.2"/></svg>
        tomas@kelvarin.com.au
      </li>
      <li>
        <svg viewBox="0 0 14 14"><circle cx="6" cy="6" r="4" fill="none" stroke="var(--brand-green)" stroke-width="1.8"/><path d="M9,9 L13,13" stroke="var(--brand-green)" stroke-width="2"/></svg>
        www.kelvoria.com.au
      </li>
    </ul>

    <div class="brand">
      <span class="brand__dot"></span>
      <span class="brand__name">Kelvoria</span>
    </div>

    <div class="location">
      <svg viewBox="0 0 16 20"><path d="M8,1 C4,1 1.5,4 1.5,7.5 C1.5,12 8,19 8,19 C8,19 14.5,12 14.5,7.5 C14.5,4 12,1 8,1 Z" fill="var(--brand-green)"/><circle cx="8" cy="7.5" r="2.5" fill="#fff"/></svg>
      <span>Melbourne,<br>Australia</span>
    </div>
  </section>

  <section class="card card--back" aria-label="Business card back">
    <div class="river-photo" role="img" aria-label="Photograph of the Yarra River in Melbourne with the city skyline"></div>
  </section>

</main>
</body>
</html>
```